New B2C website design to help dads be better dads

DadHarbor is a website to help dads be the “best dad you can be.”

We require our website to be designed into a PSD format, no coding necessary.

The general concept is a two-page design. The first page is the login page, the second page is the home page. Once at the home page, rather than navigating to and from different pages, the user will push and pull through different visual and functional layers of the hierarchy. In theory, this should add to the user experience by having a visual anchor of where they are (through layered pagination) as well as improving loading times since the new information should only be a delta in data load versus a brand new page load.

The general look-and-feel we are going for is clean, simple, minimal. This means that the winning design will show us a good eye for web-optimized typography, good use of white (negative) space, and good use of a visually pleasing grid.

We require a total of 6 page "views" plus the landing page. We note that many of the views are similar to one another.
Landing page
Milestone view
Task view
Content view, articles
Content view, products
Search view
What's new view

Please review all of the additional information provided as well as the attachments for examples.

We provide the following websites as good references for:

Typography:
http://example-kelvorn.com/journal/

Use of white space:
http://www.trenvaskit.com/
http://moldrefin.com/

Example for “scrolling” page concept as well as good balance of color, typography, and white space:
http://www.qorbitalmeet.eu/

Please contact us with questions so that we can guide your design effort.
Updates

Hello designers,

The following information is added to help guide the design process:

1.  For the text dialogue below the landing page, please assume the following word count:
"why are we making dad harbor?": 250 words
"who are we?" 200 words
"what's the deal with the penguin logo?" 300 words

For the social media links, please see http://www.gravelplumbs.com/
Notice the floating "social" bar that is always to the right.  This is the concept we are going for, please try to implement this as you see fit. 

Target Market(s)

Fathers of young children ages 0-6 years old.

Industry/Entity Type

Product

Font styles to use
Sans Serif

Requirements
Must have
• Clean lines, minimal design concept

Incorporation of our logo (see attached document)

Header content is static for all views after landing page, see example

This page WILL be responsive, please keep that in mind when designing
The timeline bar should be to the left, with the timeline bar’s “milestones” also being responsive.

Designer is free to suggest font types, but any fonts used must be royalty-free and web-optimized. We request a minimum number of font types as well as fonts that load relatively fast. We reinforce that visually appealing typography is a significant factor in the winning design choice.

While we are not expecting the winning design to include code, please keep in mind that the final implementation needs to be optimized for desktop, tablet, and mobile platforms.

If you are using stock photography that is not generated by you, please provide where/how we can obtain imagery, as well as price.

All custom graphics must be available in original formats; Photoshop/GIMP layered files for layout design, and vector formats for logos, icons and other graphical elements.

Please incorporate “Blue” into design elements as you see fit, as the RGB 67 74 169 Blue is the primary color used in our brand. The complement to this blue is 255 202 0, a brownish orange. Feel free to use this color as well, although please keep it to a lesser amount.

Background color is your choice, do not feel the need to use the grey.
Should not have
• Excessive graphical content such that it affects loading times

Excessive use of too many font types such that it affects loading times

```html
<!DOCTYPE html>
<html lang="en">
<head>
<meta charset="utf-8">
<title>DadHarbor — Be the best dad you can be</title>
<link rel="stylesheet" href="https://fonts.googleapis.com/css2?family=Oswald:wght@500;600&family=Open+Sans:wght@300;400;600;700;800&family=Raleway:wght@300&display=swap">
<style>
  :root {
    --brand-blue: #434aa9;
    --brand-blue-dark: #1f2a6b;
    --brand-gold: #f0a81e;
    --ring-blue: #6f86e0;
    --ring-light: #9cc7ea;
    --ink: #111111;
    --paper: #ffffff;
    --field: #ffffff;
  }
  * { box-sizing: border-box; margin: 0; padding: 0; }
  html, body { width: 1200px; height: 3057px; overflow: hidden; background: var(--paper); }
  body { font-family: "Open Sans", Arial, sans-serif; color: var(--ink); position: relative; }

  /* Hero */
  .hero { position: absolute; left: 0; top: 0; width: 1200px; height: 706px; }
  .hero-photo {
    position: absolute; inset: 0;
    background:
      radial-gradient(ellipse at 30% 20%, #c7d98a 0%, rgba(199,217,138,0) 45%),
      radial-gradient(ellipse at 75% 45%, #9b6a4c 0%, rgba(155,106,76,0) 50%),
      radial-gradient(ellipse at 45% 85%, #5e4a3a 0%, rgba(94,74,58,0) 45%),
      linear-gradient(160deg, #8fb348 0%, #6f9a3a 40%, #7a6244 75%, #5a4a3c 100%);
  }
  .brand { position: absolute; left: 30px; top: 70px; display: flex; align-items: center; gap: 10px; }
  .brand-dot { width: 34px; height: 34px; border-radius: 50%; background: var(--brand-blue-dark); }
  .brand-name { font-weight: 800; font-size: 22px; color: var(--brand-blue-dark); }

  .tagline {
    position: absolute; left: 30px; top: 168px; width: 704px; height: 117px;
    background: rgba(255,255,255,0.72); border-radius: 6px; padding: 10px 14px;
    white-space: nowrap; overflow: hidden;
  }
  .tagline h1 {
    font-family: "Oswald", sans-serif; font-weight: 600; font-size: 50px; line-height: 56px;
    color: var(--brand-gold); letter-spacing: 0.3px;
  }
  .tagline p { font-weight: 600; font-size: 25px; line-height: 34px; color: var(--brand-blue-dark); }

  .login {
    position: absolute; left: 25px; top: 306px; width: 306px; height: 249px;
    background: rgba(255,255,255,0.35); border-radius: 6px; padding: 20px 16px;
  }
  .login-field {
    height: 46px; background: var(--field); border: 2px solid #c9cde6; border-radius: 6px;
    display: flex; align-items: center; gap: 8px; padding: 0 12px; margin-bottom: 23px;
    font-weight: 700; font-size: 15px; color: var(--brand-blue-dark);
  }
  .login-field svg { width: 16px; height: 16px; }
  .login-forgot { font-size: 12px; font-weight: 600; color: var(--ink); margin: -6px 0 14px; }
  .login-actions { display: flex; gap: 10px; }
  .btn {
    height: 53px; background: var(--brand-blue-dark); color: var(--paper); border-radius: 5px;
    font-size: 13px; font-weight: 700; display: flex; align-items: center; justify-content: center;
    text-transform: uppercase;
  }
  .btn-signin { width: 112px; }
  .btn-request { width: 153px; }

  .share-bar {
    position: absolute; right: 0; top: 183px; width: 61px; height: 255px;
    background: rgba(255,255,255,0.8); border-radius: 8px 0 0 8px;
    display: flex; flex-direction: column; align-items: center; padding-top: 12px; gap: 13px;
  }
  .share-bar span { font-size: 11px; font-weight: 600; }
  .share-dot { width: 46px; height: 46px; border-radius: 50%; background: var(--brand-blue-dark); }

  .hero-pager { position: absolute; left: 540px; top: 658px; width: 120px; height: 48px; }

  /* About */
  .about-title {
    position: absolute; left: 0; top: 758px; width: 1200px; text-align: center;
    font-weight: 800; font-size: 40px; color: var(--brand-blue); text-transform: uppercase;
  }

  .story { position: absolute; left: 0; width: 1200px; overflow: hidden; }
  .story h2 { font-weight: 300; font-size: 44px; line-height: 54px; white-space: nowrap; }
  .story p { font-weight: 600; font-size: 14px; line-height: 22.5px; margin-top: 14px; }
  .story-copy { position: absolute; left: 30px; width: 620px; }

  .story-why { top: 861px; height: 642px; background: linear-gradient(90deg, #f4f4f4 0%, #e9ebef 55%, #dfe3ea 100%); }
  .story-why .story-copy { top: 58px; }
  .story-why .story-photo {
    position: absolute; left: 672px; top: 55px; width: 520px; height: 520px; border-radius: 50%;
    border: 8px solid var(--ring-blue);
    background: radial-gradient(circle at 40% 45%, #d9b49a 0%, #c49a7e 25%, #9fb2d9 55%, #e6ecf6 100%);
  }

  .story-who { top: 1503px; height: 650px; background: linear-gradient(90deg, #f2f4f7 0%, #e5ecf5 55%, #d6e5f3 100%); }
  .story-who .story-copy { top: 60px; }
  .story-who .story-photo {
    position: absolute; left: 680px; top: 70px; width: 505px; height: 505px; border-radius: 50%;
    border: 8px solid var(--ring-light);
    background: linear-gradient(180deg, #6e9cc8 0%, #3d79b8 45%, #5ab3d6 70%, #4e5a6a 100%);
  }

  .story-logo { top: 2153px; height: 650px; background: var(--brand-blue); color: var(--paper); }
  .story-logo .story-copy { top: 66px; width: 640px; }
  .story-logo p { line-height: 23px; }

  /* Footer */
  .contact { position: absolute; left: 0; top: 2803px; width: 1200px; height: 254px; text-align: center; }
  .contact-label { margin-top: 48px; font-size: 14px; font-weight: 700; letter-spacing: 4px; text-transform: uppercase; }
  .contact-title { margin-top: 18px; font-family: "Raleway", sans-serif; font-weight: 300; font-size: 38px; letter-spacing: 1px; }
  .contact-email { margin-top: 14px; font-size: 17px; font-weight: 700; color: var(--brand-blue); }
  .contact-legal { margin-top: 30px; font-size: 11px; }
</style>
</head>
<body>

<header class="hero">
  <div class="hero-photo" role="img" aria-label="Photo of a father lying in the grass playing with his young child"></div>

  <div class="brand">
    <span class="brand-dot"></span>
    <span class="brand-name">DadHarbor</span>
  </div>

  <div class="tagline">
    <h1>BE THE BEST DAD YOU CAN BE</h1>
    <p>The portal created exclusively for dads, by dads</p>
  </div>

  <form class="login">
    <div class="login-field">
      <svg viewBox="0 0 16 16"><circle cx="8" cy="5" r="3.5" fill="#1f2a6b"/><path d="M1 16c0-4 3-6 7-6s7 2 7 6z" fill="#1f2a6b"/></svg>
      Username
    </div>
    <div class="login-field">
      <svg viewBox="0 0 16 16"><circle cx="5" cy="6" r="4" fill="none" stroke="#1f2a6b" stroke-width="2"/><path d="M8 8l7 7M12 12l2-2" stroke="#1f2a6b" stroke-width="2"/></svg>
      Password
    </div>
    <div class="login-forgot">&#9656; Forgot login?</div>
    <div class="login-actions">
      <div class="btn btn-signin">Sign in</div>
      <div class="btn btn-request">Request access</div>
    </div>
  </form>

  <aside class="share-bar">
    <span>Share</span>
    <div class="share-dot"></div>
    <div class="share-dot"></div>
    <div class="share-dot"></div>
    <div class="share-dot"></div>
  </aside>

  <svg class="hero-pager" viewBox="0 0 120 48">
    <path d="M8 20l8 8-8 8" fill="none" stroke="#fff" stroke-width="3" transform="rotate(180 12 28)"/>
    <rect x="30" y="0" width="60" height="48" fill="#fff"/>
    <path d="M44 16l16 14 16-14" fill="none" stroke="#434aa9" stroke-width="5"/>
    <path d="M44 26l16 14 16-14" fill="none" stroke="#434aa9" stroke-width="5"/>
    <path d="M104 20l8 8-8 8" fill="none" stroke="#fff" stroke-width="3"/>
  </svg>
</header>

<h2 class="about-title">About Dad Harbor</h2>

<section class="story story-why">
  <div class="story-copy">
    <h2>Why are we making dad harbor?</h2>
    <p>Lorem ipsum dolor sit amet, consectetur adipisicing elit, sed do eiusmod tempor incididunt ut labore et dolore magna aliqua. Ut enim ad minim veniam, quis nostrud exercitation ullamco laboris nisi ut aliqip ex ea comodo consequat. Duis aute irure dolor in reprehenderit in voluptate velit esse cillum dolore eu fugiat nulla pariatur. Excepteur sint occaecat cupidatat non proident, sunt in culpa qui officia deserunt mollit anim id est laborum. Lorem ipsum dolor sit amet, consectetur adipisicing elit, sed do eiusd tmor incididunt ut labore et doore magna aliqua. Ut enim ad minim veniam, quis nostrud exercitation ullamco laboris nisi ut aliquip ex ea comodo consequat. Duis aute irure dolor in rehederit in volute velit esse cillum dolore eu fugiat nulla paiatur. Excpteur sint occaecat cidatat non proident, sunt in culpa qui officia deserunt molit anim id est laborum. Lorem ipsum dolor sit amet, conttur adiscing elit, sed do eiusmod tempor incidunt ut labore et dolore magna aliqua. Ut enim ad mnim veniam, quis nostrud exercitation ullmco laboris nisi ut aliquip ex ea commodo consequat. Duis aute irure door in reprehederit in voluptate velit esse cillum doore eu fugiat nulla pariatur. Excepteur sint occaecat cupidat non proident, sunt in culpa. ea commodo consequat. Duis aute irure door in reprehenderit in voluptate velit esse cillum doore eu fugiat nulla pariatur. Excepteur sint occaecat cupidatat non proident, sunt in culpa.</p>
  </div>
  <div class="story-photo" role="img" aria-label="Circular photo of a smiling father carrying his son on his back"></div>
</section>

<section class="story story-who">
  <div class="story-copy">
    <h2>Who are we?</h2>
    <p>Lorem ipsum dolor sit amet, consectetur adipisicing elit, sed do eiusmod tempor incididunt ut labore et dolore magna aliqua. Ut enim ad minim veniam, quis nostrud exercitation ullamco laboris nisi ut aliqip ex ea comodo consequat. Duis aute irure dolor in reprehenderit in voptate velit esse cillum dolore eu fugiat nulla pariatur. Excepteur sint occaecat cupidatat non proident, sunt in culpa qui officia deserunt mollit anim id est laborum. Lorem ipsum dolor sit amet, consectetur adipisicing elit, sed do eiusd tmor incididunt ut labore et doore magna aliqua. Ut enim ad minim veniam, quis nostrud exercitation ullamco laboris nisi ut aliquip ex ea comodo consequat. Duis aute irure dolor in reheerit in volute velit esse cillum dolore eu fugiat nulla paiatur. Excpteur sint occaecat cidatat non proident, sunt in culpa qui officia deserunt molit anim id est laborum. Lorem ipsum dolor sit amet, conttur adiscing elit, sed do eiusmod tempor incidunt ut labore et dolore magna aliqua. Ut enim ad mnim veniam, quis nostrud exercitation ullmco laboris nisi ut aliquip ex ea commodo consequat. Duis aute irure door in reprehenderit in voluptate velit esse cillum doore eu fugiat nulla pariatur. Excepteur sint occaecat cupidatat non proident, sunt in culpa.</p>
  </div>
  <div class="story-photo" role="img" aria-label="Circular photo of a father sitting by the sea with two young children in sun hats"></div>
</section>

<section class="story story-logo">
  <div class="story-copy">
    <h2>What's the deal with the<br>penguin logo?</h2>
    <p>Lorem ipsum dolor sit amet, consectetur adipisicing elit, sed do eiusmod tempor incididunt ut labore et dolore magna aliqua. Ut enim ad minim veniam, quis nostrud exercitation ullamco laboris nisi ut aliqip ex ea comodo consequat. Duis aute irure dolor in reprehenderit in voptate velit esse cillum dolore eu fugiat nulla pariatur. Excepteur sint occaecat cupidatat non proident, sunt in culpa qui officia deserunt mollit anim id est laborum. Lorem ipsum dolor sit amet, consectetur adipisicing elit, sed do eiusd tmor incididunt ut labore et doore magna aliqua. Ut enim ad minim veniam, quis nostrud exercitation ullamco laboris nisi ut aliquip ex ea comodo consequat. Duis aute irure dolor in reheerit in volute velit esse cillum dolore eu fugiat nulla paiatur. Excpteur sint occaecat cidatat non proident, sunt in culpa qui officia deserunt molit anim id est laborum. Lorem ipsum door sit met, conttur adiscing elit, sed do eiusmod tempor incidunt ut labore et dolore magna aliqua. Ut enim ad mnim veniam, quis nostrud exercitation ullmco laboris nisi ut aliquip ex ea commodo consequat. Duis aute irure door in reprehenderit in voluptate velit esse cillum doore eu fugiat nulla pariatur. Excepteur sint occaecat cupidatat non proident, sunt in culpa. fugiat nulla pariatur. Excepteur sint occaecat cupiatat non proident, sunt in culpa.</p>
  </div>
</section>

<footer class="contact">
  <div class="contact-label">Contact</div>
  <div class="contact-title">GET IN TOUCH</div>
  <div class="contact-email">info@dadharbor.example</div>
  <div class="contact-legal">Privacy Policy &nbsp;|&nbsp; &copy; 2013 DadHarbor &nbsp;|&nbsp; Terms Policy &nbsp;|&nbsp; Disclaimer</div>
</footer>

</body>
</html>
```